Motivational Poster Design Project

I would like to create a poster with some of my favorite quotes to hang in my office. I did a similar project in 2012 and I've uploaded the top 2 designs so you can get a better idea of what I'm looking for. I will provide feedback on your design within 24 hours of receiving it.

The poster must contain the following quotes:

"You’re only given a little spark of madness. You mustn’t lose it.”
- Dorian Fletcher

“The most contrarian thing of all is not to oppose the crowd but to think for yourself.”
- Marcus Olden

"I constantly see people rise in life who are not the smartest, sometimes not even the most diligent, but they are learning machines. They go to bed every night a little wiser than they were when they got up and boy does that help, particularly when you have a long run ahead of you."
- Frankie Dalgarth

“In theory, there’s no difference between theory and practice. But, in practice, there is.”
- Kees R. T. Ter Haverkamp

"At the end of the day, a reactionary life is a normal life. One thing is consistent in every remarkable person: they decide to do something remarkable. Don’t let the world choose who you become."
- Rohan Kapadia

“It usually takes 3-4 months to try enough that you can do a proper 80/20 analysis, then two months to design systems to scale what *is* working.”
-Ned Yarrow

“Authority is 20 percent given, 80 percent taken.”
- Glenn Mosbacker

“Your actions are consistent with the way the world occurs to you.”
- Dieter Kolbach

Project Deadline Extended
Reason: I am going to be travelling with no access to internet until January 5th, 2015. I am extending the project deadline until 12/31/14 and I'll make a final decision during the 1st week of January.

Target Market(s)

Personal Project

Industry/Entity Type

Learning

Requirements
Must have
• The poster will be 24" high x 36" long and printed on canvas, so the image you create needs to have a resolution of at least 2700 x 3900.
Nice to have
• I don't have an exact vision for how the poster should look, so I am totally open to you using your creativity to develop, arrange and present the content as you'd like.
• That said, I would like an image (photo or posterized image) of the person being quoted along with each quote. I do not have specific images that I would like you to use, so you will need to find the images on your own. The images don't need to be perfect... I am more interested in the poster relating the essence of the quotes and the people being quoted than I am in perfect photographic images of the people being quoted.

```html
<!DOCTYPE html>
<html lang="en">
<head>
<meta charset="utf-8">
<title>Quote Poster</title>
<link rel="stylesheet" href="https://fonts.googleapis.com/css2?family=Alfa+Slab+One&family=Amatic+SC:wght@700&family=Arvo:wght@700&family=Dancing+Script:wght@500&family=Delius&family=Handlee&family=Herr+Von+Muellerhoff&family=Oswald:wght@500&family=Sacramento&display=swap">
<style>
  :root {
    --backdrop: #cfcfcf;
    --board: #1c1c1c;
    --board-light: #2a2a2a;
    --frame: #b9b9b9;
    --chalk: #e6e6e6;
    --chalk-dim: #9a9a9a;
    --yellow: #e2d77a;
    --pink: #e58aa6;
    --blue: #9fc8e6;
    --orange: #e9a94a;
    --green: #cfe07a;
    --violet: #b9a1e0;
    --gold: #d8b15c;
    --panel: #474747;
    --portrait: #4b4b4b;
  }
  * { box-sizing: border-box; margin: 0; padding: 0; }
  html, body { width: 1200px; height: 1000px; overflow: hidden; }
  body { background: var(--backdrop); position: relative; }

  .poster {
    position: absolute; left: 280px; top: 20px; width: 640px; height: 960px;
    background: radial-gradient(ellipse at 50% 40%, var(--board-light), var(--board) 75%);
    border: 6px solid var(--frame);
  }
  .poster-inner-frame { position: absolute; inset: 6px; border: 1px solid rgba(230,230,230,.35); }
  .abs { position: absolute; white-space: nowrap; }
  .portrait {
    position: absolute;
    background: radial-gradient(ellipse at 50% 45%, #6a6a6a, var(--portrait) 55%, rgba(28,28,28,0) 80%);
  }
  .ornament-band {
    position: absolute; left: 60px; width: 520px; height: 10px;
    background: linear-gradient(90deg, rgba(200,200,200,0), rgba(200,200,200,.45), rgba(200,200,200,0));
  }
  .flourish { position: absolute; background: rgba(200,200,200,.18); }
  .signature {
    position: absolute; font-family: "Herr Von Muellerhoff", cursive;
    color: var(--chalk); font-size: 22px; white-space: nowrap; line-height: 1;
  }

  .quote-spark { left: 140px; top: 72px; width: 250px; text-align: center;
    font-family: "Arvo", serif; color: var(--yellow); font-size: 14px; line-height: 20px; }
  .quote-spark .big { font-size: 18px; line-height: 24px; }

  .quote-crowd { left: 212px; top: 176px; width: 296px; text-align: center;
    font-family: "Amatic SC", cursive; color: var(--pink); font-size: 19px; line-height: 22px; }

  .learning-panel { left: 38px; top: 252px; width: 552px; height: 120px; background: var(--panel); opacity: .85; }
  .quote-learning { left: 62px; top: 266px;
    font-family: "Handlee", cursive; color: var(--blue); font-size: 10.5px; line-height: 17px; }

  .quote-theory { left: 200px; top: 382px; width: 282px; text-align: right;
    font-family: "Oswald", sans-serif; color: var(--orange); font-size: 15px; line-height: 20px; }

  .remarkable-box { left: 51px; top: 482px; width: 539px; height: 104px; border: 1px solid var(--chalk-dim); }
  .quote-remarkable { left: 86px; top: 490px;
    font-family: "Delius", cursive; color: var(--green); font-size: 10.5px; line-height: 16px; }
  .remarkable-rule { left: 235px; top: 577px; width: 350px; height: 1px; background: var(--chalk-dim); }

  .quote-systems { left: 140px; top: 600px; width: 420px; text-align: right;
    font-family: "Dancing Script", cursive; color: var(--violet); font-size: 17px; line-height: 25px; }

  .authority-frame { left: 80px; top: 715px; width: 480px; height: 100px; border: 1px solid rgba(200,200,200,.35); border-radius: 14px; }
  .quote-authority { left: 145px; top: 734px; width: 270px; text-align: center;
    font-family: "Alfa Slab One", serif; color: var(--chalk); line-height: 1; }
  .quote-authority .line-one { font-size: 24px; letter-spacing: 2px; display: block; }
  .quote-authority .line-two { font-family: "Arvo", serif; font-size: 14px; display: block; margin-top: 5px; }
  .signature.small { font-size: 18px; }

  .quote-actions { left: 200px; top: 830px;
    font-family: "Sacramento", cursive; color: var(--gold); font-size: 21px; line-height: 22px; }
  .quote-actions .indent { padding-left: 22px; }
</style>
</head>
<body>
<main class="poster">
  <div class="poster-inner-frame"></div>

  <div class="ornament-band" style="top:38px" role="img" aria-label="Chalk-drawn decorative border band"></div>
  <div class="flourish" style="left:72px;top:92px;width:42px;height:52px" role="img" aria-label="Chalk flourish"></div>
  <div class="flourish" style="left:522px;top:92px;width:42px;height:52px" role="img" aria-label="Chalk flourish"></div>

  <p class="abs quote-spark">"You're only given a<br>little spark of madness.<br><span class="big">You mustn't lose it."</span></p>
  <span class="signature" style="left:268px;top:130px">Dorian Fletcher</span>
  <div class="portrait" style="left:408px;top:58px;width:66px;height:92px" role="img" aria-label="Portrait of Dorian Fletcher"></div>

  <div class="portrait" style="left:118px;top:160px;width:66px;height:72px" role="img" aria-label="Portrait of Marcus Olden"></div>
  <p class="abs quote-crowd">"The most contrarian thing of all is not to<br>oppose the crowd but to think for yourself."</p>
  <span class="signature" style="left:380px;top:222px">Marcus Olden</span>

  <div class="abs learning-panel"></div>
  <p class="abs quote-learning">"I constantly see people rise in life who are not the smartest,<br>sometimes not even the most diligent, but they are learning machines.<br>They go to bed every night a little wiser than they were when they got up<br>and boy does that help, particularly when you have a long run ahead of you."</p>
  <span class="signature" style="left:85px;top:340px">Frankie Dalgarth</span>
  <div class="portrait" style="left:508px;top:264px;width:64px;height:92px" role="img" aria-label="Portrait of Frankie Dalgarth"></div>

  <div class="portrait" style="left:138px;top:376px;width:66px;height:100px" role="img" aria-label="Portrait of Kees R. T. Ter Haverkamp"></div>
  <p class="abs quote-theory">"In theory, there's no difference<br>between theory and practice.<br>But, in practice, there is."</p>
  <span class="signature" style="left:285px;top:448px">Kees R. T. Ter Haverkamp</span>

  <div class="abs remarkable-box"></div>
  <p class="abs quote-remarkable">"At the end of the day, a reactionary life is a normal life.<br>One thing is consistent in every remarkable person:<br>they decide to do something remarkable.<br>Don't let the world choose who you become."</p>
  <span class="signature" style="left:102px;top:558px">Rohan Kapadia</span>
  <div class="abs remarkable-rule"></div>
  <div class="portrait" style="left:468px;top:486px;width:72px;height:84px" role="img" aria-label="Portrait of Rohan Kapadia"></div>

  <div class="portrait" style="left:66px;top:600px;width:68px;height:96px" role="img" aria-label="Portrait of Ned Yarrow"></div>
  <p class="abs quote-systems">"It usually takes 3-4 months to try enough that you can<br>do a proper 80/20 analysis, then two months to<br>design systems to scale what is working."</p>
  <span class="signature" style="left:455px;top:676px">Ned Yarrow</span>

  <div class="abs authority-frame"></div>
  <p class="abs quote-authority"><span class="line-one">"AUTHORITY IS</span><span class="line-two">20% GIVEN, 80% TAKEN."</span></p>
  <span class="signature small" style="left:282px;top:784px">Glenn Mosbacker</span>
  <div class="portrait" style="left:442px;top:720px;width:70px;height:88px" role="img" aria-label="Portrait of Glenn Mosbacker"></div>

  <div class="portrait" style="left:124px;top:826px;width:62px;height:78px" role="img" aria-label="Portrait of Dieter Kolbach"></div>
  <p class="abs quote-actions">"Your actions are consistent with<br><span class="indent">the way the world occurs to you."</span></p>
  <span class="signature" style="left:362px;top:874px">Dieter Kolbach</span>

  <div class="ornament-band" style="top:908px" role="img" aria-label="Chalk-drawn decorative border band"></div>
</main>
</body>
</html>
```